Commercial Real Estate

We need a business card design for a new commercial real estate business that specializes in apartment building brokerage. Not individual units but the entire complex. We find and represent the owners existing buildings and well as new buyers for those buildings. The design should convey trust, integrity, knowledge and growth. It should be easily read.

Target Market(s)

40 to 65 years old

Industry/Entity Type

Real Estate

```html
<!DOCTYPE html>
<html lang="en">
<head>
<meta charset="utf-8">
<title>Stonebay Property Investments – Business Card</title>
<link rel="stylesheet" href="https://fonts.googleapis.com/css2?family=Open+Sans:wght@400;600;700&display=swap">
<style>
  :root {
    --page-bg: #d9d6d2;
    --card-white: #ffffff;
    --card-shade: #eeeeee;
    --slate: #5e6a6b;
    --slate-dark: #4c5556;
    --teal: #6ccfcf;
    --text: #3f4546;
    --rule: #7a8283;
  }
  * { box-sizing: border-box; margin: 0; padding: 0; }
  html, body {
    width: 1200px; height: 900px; overflow: hidden;
    background: var(--page-bg);
    font-family: "Open Sans", Arial, sans-serif;
  }
  .card {
    position: absolute; left: 75px; top: 150px;
    width: 1050px; height: 600px;
    background: linear-gradient(160deg, var(--card-white) 0%, var(--card-shade) 100%);
    box-shadow: 0 14px 34px rgba(0,0,0,0.22);
    overflow: hidden;
  }
  .swoosh { position: absolute; inset: 0; width: 1050px; height: 600px; }
  .brand {
    position: absolute; left: 64px; top: 178px;
    display: flex; align-items: center; gap: 16px;
  }
  .brand-square { width: 26px; height: 26px; background: var(--teal); }
  .brand-text { color: var(--slate); font-weight: 700; }
  .brand-name { font-size: 42px; letter-spacing: 3px; line-height: 1; }
  .brand-tag { font-size: 15px; letter-spacing: 2px; margin-top: 6px; }
  .divider {
    position: absolute; left: 64px; top: 300px;
    width: 720px; height: 2px; background: var(--rule);
  }
  .person {
    position: absolute; right: 190px; top: 220px; text-align: right;
    color: var(--text);
  }
  .person-name { font-size: 27px; font-weight: 700; letter-spacing: 1px; color: var(--slate); }
  .person-role { font-size: 17px; letter-spacing: 1px; margin-top: 2px; }
  .contacts {
    position: absolute; left: 64px; top: 350px; list-style: none;
    color: var(--text); font-size: 21px;
  }
  .contacts li { display: flex; align-items: center; gap: 16px; height: 44px; }
  .contacts svg { width: 22px; height: 22px; fill: var(--slate-dark); flex: none; }
  .website {
    position: absolute; left: 945px; top: 505px;
    color: #ffffff; font-size: 16px; letter-spacing: 2px; line-height: 1;
    white-space: nowrap;
    transform: translate(-50%, -50%) rotate(-30deg);
  }
</style>
</head>
<body>
  <div class="card">
    <svg class="swoosh" viewBox="0 0 1050 600" aria-hidden="true">
      <path d="M1050,100 C990,320 860,500 640,600 L1050,600 Z" fill="var(--teal)"/>
      <path d="M1050,145 C995,335 880,510 700,600 L1050,600 Z" fill="var(--card-white)"/>
      <path d="M1050,165 C1002,350 900,515 735,600 L1050,600 Z" fill="var(--slate)"/>
    </svg>

    <div class="brand">
      <span class="brand-square"></span>
      <div class="brand-text">
        <div class="brand-name">STONEBAY</div>
        <div class="brand-tag">Property Investments</div>
      </div>
    </div>

    <div class="person">
      <div class="person-name">DANIEL HARWOOD</div>
      <div class="person-role">FINANCIAL ADVISOR</div>
    </div>

    <div class="divider"></div>

    <ul class="contacts">
      <li>
        <svg viewBox="0 0 24 24"><path d="M7 1h10a2 2 0 0 1 2 2v18a2 2 0 0 1-2 2H7a2 2 0 0 1-2-2V3a2 2 0 0 1 2-2zm0 3v14h10V4zm5 15.5a1.2 1.2 0 1 0 0 2.4 1.2 1.2 0 0 0 0-2.4z"/></svg>
        012 555 0147
      </li>
      <li>
        <svg viewBox="0 0 24 24"><path d="M6.6 10.8a15.2 15.2 0 0 0 6.6 6.6l2.2-2.2a1 1 0 0 1 1-.25 11.4 11.4 0 0 0 3.6.57 1 1 0 0 1 1 1V20a1 1 0 0 1-1 1A17 17 0 0 1 3 4a1 1 0 0 1 1-1h3.5a1 1 0 0 1 1 1c0 1.25.2 2.450.57 3.6a1 1 0 0 1-.25 1z"/></svg>
        012 555 0148
      </li>
      <li>
        <svg viewBox="0 0 24 24"><path d="M2 5h20v14H2zm2 2v.5l8 5 8-5V7zm0 2.8V17h16V9.8l-8 5z"/></svg>
        contact@stonebay.com
      </li>
      <li>
        <svg viewBox="0 0 24 24"><path d="M12 1a7.5 7.5 0 0 0-7.5 7.5C4.5 14 12 23 12 23s7.5-9 7.5-14.5A7.5 7.5 0 0 0 12 1zm0 10.2a2.7 2.7 0 1 1 0-5.4 2.7 2.7 0 0 1 0 5.4z"/></svg>
        21, 4th Floor, Elm Court Road KRV
      </li>
    </ul>

    <div class="website">www.stonebay.com</div>
  </div>
</body>
</html>
```